Heritage Hollow Business Cards

Require a business card design. <br/><br/>Needs to include logo (either round or long version) plus these details:<br/>Maya Torvell<br/>Heritage Hollow<br/>maya@kelvadtrading.com.au<br/>02 6481 7395<br/>PO Box Glenwarra NSW 2791<br/>www.heritagehollow.com.au<br/><br/>I need in an editable format so that I can create for multiple staff members. <br/><br/>

Target Market(s)

We are an online store selling renovation products to home owners are builders. Looking for a classic classy design.

Industry/Entity Type

Home And Garden

Contact Information for Business Card

Maya Torvell
Heritage Hollow
maya@kelvadtrading.com.au
02 6481 7395
PO Box Glenwarra NSW 2791
www.heritagehollow.com.au

Colors

Designer to choose colors to be used in the design.

Requirements
Must have
• Must include Logo.

```html
<!DOCTYPE html>
<html lang="en">
<head>
<meta charset="utf-8">
<title>Heritage Hollow Business Cards</title>
<link rel="stylesheet" href="https://fonts.googleapis.com/css2?family=Josefin+Slab:wght@400;600&display=swap">
<style>
  :root {
    --backdrop: #8c8c8c;
    --card-light: #ffffff;
    --card-dark: #2b2b2b;
    --ink: #2e2e2e;
    --ink-soft: #9a9a9a;
    --rule: #8a8a8a;
    --on-dark: #f2f2f2;
  }
  * { margin: 0; padding: 0; box-sizing: border-box; }
  html, body {
    width: 1200px; height: 960px; overflow: hidden;
    background: var(--backdrop);
    font-family: "Josefin Slab", Georgia, serif;
  }
  .canvas { position: relative; width: 1200px; height: 960px; }
  .card { position: absolute; left: 281px; width: 655px; height: 373px; }
  .card--front { top: 59px; background: var(--card-light); color: var(--ink); }
  .card--back { top: 501px; background: var(--card-dark); }

  .brand {
    position: absolute; left: 56px; top: 136px;
    display: flex; align-items: center; gap: 10px; white-space: nowrap;
  }
  .brand__dot {
    width: 28px; height: 28px; border-radius: 50%;
    border: 1.5px solid var(--ink); flex: none;
  }
  .brand__name { font-size: 30px; font-weight: 600; color: var(--ink); line-height: 1; }

  .person { position: absolute; left: 68px; top: 210px; white-space: nowrap; }
  .person__name { font-size: 20px; font-weight: 600; letter-spacing: 0.2px; text-transform: uppercase; line-height: 1.2; }
  .person__role { font-size: 17px; color: var(--ink-soft); margin-top: 5px; letter-spacing: 0.3px; }

  .divider {
    position: absolute; left: 234px; top: 213px; bottom: 0;
    width: 1px; background: var(--rule);
  }

  .contact { position: absolute; left: 253px; top: 208px; white-space: nowrap; }
  .contact__company { font-size: 15px; color: var(--ink); letter-spacing: 0.3px; height: 22px; }
  .contact__address { font-size: 15px; color: var(--ink-soft); letter-spacing: 0.5px; height: 30px; line-height: 26px; }
  .contact__line {
    display: flex; align-items: center; gap: 7px;
    font-size: 14px; color: var(--ink-soft); letter-spacing: 0.4px; height: 24px;
  }
  .contact__icon { width: 12px; height: 12px; flex: none; }

  .seal {
    position: absolute; left: 50%; top: 50%;
    width: 230px; height: 230px; margin: -115px 0 0 -115px;
    border: 1.5px solid var(--on-dark); border-radius: 50%;
    display: flex; align-items: center; justify-content: center; text-align: center;
  }
  .seal__name { font-size: 31px; font-weight: 600; line-height: 1.05; color: var(--on-dark); }
</style>
</head>
<body>
<main class="canvas">
  <section class="card card--front">
    <div class="brand">
      <span class="brand__dot"></span>
      <span class="brand__name">Heritage Hollow</span>
    </div>

    <div class="person">
      <p class="person__name">Maya Torvell</p>
      <p class="person__role">Founder &amp; CEO</p>
    </div>

    <div class="divider"></div>

    <div class="contact">
      <p class="contact__company">Heritage Hollow</p>
      <p class="contact__address">PO Box Glenwarra NSW 2791</p>
      <p class="contact__line">
        <svg class="contact__icon" viewBox="0 0 16 16" aria-hidden="true"><path d="M4 1.5l2.3 3-1.4 1.6c.9 2 2.6 3.8 4.9 5l1.6-1.4 3 2.3-1.6 2.5C7.5 14.3 1.8 8.6 1.5 3z" fill="#2e2e2e"/></svg>
        02 6481 7395
      </p>
      <p class="contact__line">
        <svg class="contact__icon" viewBox="0 0 16 16" aria-hidden="true"><rect x="1" y="3.5" width="14" height="9" fill="#2e2e2e"/><path d="M1.5 4l6.5 5 6.5-5" stroke="#fff" stroke-width="1.2" fill="none"/></svg>
        maya@kelvadtrading.com.au
      </p>
      <p class="contact__line">
        <svg class="contact__icon" viewBox="0 0 16 16" aria-hidden="true"><g fill="none" stroke="#2e2e2e" stroke-width="1.2"><circle cx="8" cy="8" r="6.5"/><ellipse cx="8" cy="8" rx="2.8" ry="6.5"/><path d="M1.5 8h13M2.6 4.6h10.8M2.6 11.4h10.8"/></g></svg>
        www.heritagehollow.com.au
      </p>
    </div>
  </section>

  <section class="card card--back">
    <div class="seal">
      <span class="seal__name">Heritage<br>Hollow</span>
    </div>
  </section>
</main>
</body>
</html>
```